Etiketten-Design für Kräuterbonbon-Metalldose
Katrin Wolber hat sehr viel Talent. Das Design ist absolut kreativ.
Zielgruppe
Unsere Firma FelvoNat verkauft verschiedene Sorten Kräuterbonbons.
Wir brauchen ein Etikett, dass auf eine Metall-Dose (Durchmesser 10 cam, Höhe ca. 3 cm) geklebt wird.
Zielgruppe: jung-alt
Aufgabenstellung
Der Name unserer Kräuterbonbons ist Moospille.
Wir möchten, dass unsere Kunden, wenn sie das Etikett sehen einen Bezug zur Schweiz herstellen können.
Wir verwenden für unsere Bonbons unterschiedliche Kräuter für verschiedene Anwendungen:
Konkret sind erstmal 4 Dosen geplant:
-Kräutermischung aus 16 Kräuter gegen Husten
-Salbei gegen Halsschmerzen
-Anis gegen Magenschmerzen
-Zitrone/Ingwer für die Nerven
Vorderseite: Produktbeschreibung
Rückseite: unsere Herstellerangaben
Größenangaben der Dose: Durchmesser 10 cm, Höhe ca. 3 cm
Im Anhang habe ich Ihnen noch weitere/ genauere Informationen zur Verfügung bereitgestellt!

```html
<!DOCTYPE html>
<html lang="de">
<head>
<meta charset="utf-8">
<title>Moospille – Dosenetiketten</title>
<link rel="stylesheet" href="https://fonts.googleapis.com/css2?family=Patrick+Hand+SC&family=Montserrat:wght@600&display=swap">
<style>
  :root {
    --brand-red: #e2131b;
    --paper: #ffffff;
    --label-white: #ffffff;
    --sage: #8f906b;
    --ginger: #f6b04e;
    --anise: #26959d;
    --herbs: #054c7d;
    --licorice: #000000;
  }
  html, body {
    margin: 0;
    padding: 0;
    width: 1200px;
    height: 4152px;
    overflow: hidden;
    background: var(--paper);
  }
  .sheet {
    position: relative;
    width: 1200px;
    height: 4152px;
  }
  .brand-mark {
    position: absolute;
    left: 426px;
    top: 218px;
    width: 300px;
    height: 300px;
  }
  .label {
    position: absolute;
    left: 295px;
    width: 600px;
    height: 600px;
  }
  .label--salbei { top: 636px; }
  .label--ingwer { top: 1327px; }
  .label--anis { top: 2020px; }
  .label--kraeuter { top: 2708px; }
  .label--lakritze { top: 3409px; }

  .brand-name {
    font-family: "Patrick Hand SC", cursive;
    font-size: 50px;
    letter-spacing: 3px;
    fill: var(--brand-red);
  }
  .brand-mark .brand-name { font-size: 56px; }
  .brand-dot { fill: var(--brand-red); }
  .tagline {
    font-family: "Montserrat", sans-serif;
    font-weight: 600;
    font-size: 18px;
    letter-spacing: 2px;
    fill: var(--brand-red);
  }
  .product-name {
    font-family: "Patrick Hand SC", cursive;
    font-size: 104px;
    letter-spacing: 4px;
    fill: var(--label-white);
  }
  .product-use {
    font-family: "Patrick Hand SC", cursive;
    font-size: 38px;
    letter-spacing: 4px;
    fill: var(--label-white);
  }
  .herb-art { opacity: 0.35; }
</style>
</head>
<body>
<main class="sheet">

  <svg class="brand-mark" viewBox="0 0 300 300" aria-label="Moospille">
    <defs>
      <path id="mark-arc" d="M58 165 a92 92 0 1 1 184 0 a92 92 0 1 1 -184 0"/>
    </defs>
    <circle class="brand-dot" cx="150" cy="165" r="82"/>
    <text class="brand-name"><textPath href="#mark-arc" startOffset="22%" text-anchor="middle">MOOSPILLE</textPath></text>
  </svg>

  <!-- Salbei -->
  <svg class="label label--salbei" viewBox="0 0 600 600">
    <defs>
      <path id="salbei-ring" d="M50 300 a250 250 0 1 0 500 0 a250 250 0 1 0 -500 0"/>
      <path id="salbei-brand" d="M200 300 a100 100 0 1 1 200 0 a100 100 0 1 1 -200 0"/>
      <path id="salbei-tag" d="M140 300 a160 160 0 1 1 320 0 a160 160 0 1 1 -320 0"/>
    </defs>
    <circle cx="300" cy="300" r="296" fill="var(--sage)"/>
    <ellipse class="herb-art" cx="95" cy="355" rx="70" ry="50" fill="#d9d6c0" role="img" aria-label="Illustration von Salbeiblättern"/>
    <circle class="brand-dot" cx="300" cy="300" r="90"/>
    <text class="brand-name"><textPath href="#salbei-brand" startOffset="20%" text-anchor="middle">MOOSPILLE</textPath></text>
    <text class="tagline"><textPath href="#salbei-tag" startOffset="21%" text-anchor="middle">TRADITIONAL SWISS FORMULA</textPath></text>
    <text class="product-name"><textPath href="#salbei-ring" startOffset="26%" text-anchor="middle">SALBEI</textPath></text>
    <text class="product-use"><textPath href="#salbei-ring" startOffset="56%" text-anchor="middle">BEI HALSSCHMERZEN</textPath></text>
  </svg>

  <!-- Ingwer-Zitrone -->
  <svg class="label label--ingwer" viewBox="0 0 600 600">
    <defs>
      <path id="ingwer-ring" d="M50 300 a250 250 0 1 0 500 0 a250 250 0 1 0 -500 0"/>
      <path id="ingwer-brand" d="M200 300 a100 100 0 1 1 200 0 a100 100 0 1 1 -200 0"/>
      <path id="ingwer-tag" d="M140 300 a160 160 0 1 1 320 0 a160 160 0 1 1 -320 0"/>
    </defs>
    <circle cx="300" cy="300" r="296" fill="var(--ginger)"/>
    <ellipse class="herb-art" cx="75" cy="250" rx="50" ry="85" fill="#fde3b4" role="img" aria-label="Illustration einer Zitronenscheibe mit Ingwer"/>
    <circle class="brand-dot" cx="300" cy="300" r="90"/>
    <text class="brand-name"><textPath href="#ingwer-brand" startOffset="20%" text-anchor="middle">MOOSPILLE</textPath></text>
    <text class="tagline"><textPath href="#ingwer-tag" startOffset="21%" text-anchor="middle">TRADITIONAL SWISS FORMULA</textPath></text>
    <text class="product-name"><textPath href="#ingwer-ring" startOffset="37%" text-anchor="middle">INGWER-ZITRONE</textPath></text>
    <text class="product-use"><textPath href="#ingwer-ring" startOffset="81%" text-anchor="middle">FÜR DIE NERVEN</textPath></text>
  </svg>

  <!-- Anis -->
  <svg class="label label--anis" viewBox="0 0 600 600">
    <defs>
      <path id="anis-ring" d="M50 300 a250 250 0 1 0 500 0 a250 250 0 1 0 -500 0"/>
      <path id="anis-brand" d="M200 300 a100 100 0 1 1 200 0 a100 100 0 1 1 -200 0"/>
      <path id="anis-tag" d="M140 300 a160 160 0 1 1 320 0 a160 160 0 1 1 -320 0"/>
    </defs>
    <circle cx="300" cy="300" r="296" fill="var(--anise)"/>
    <ellipse class="herb-art" cx="120" cy="420" rx="75" ry="70" fill="#cfe6e6" role="img" aria-label="Illustration eines Sternanis"/>
    <circle class="brand-dot" cx="300" cy="300" r="90"/>
    <text class="brand-name"><textPath href="#anis-brand" startOffset="20%" text-anchor="middle">MOOSPILLE</textPath></text>
    <text class="tagline"><textPath href="#anis-tag" startOffset="21%" text-anchor="middle">TRADITIONAL SWISS FORMULA</textPath></text>
    <text class="product-name"><textPath href="#anis-ring" startOffset="28%" text-anchor="middle">ANIS</textPath></text>
    <text class="product-use"><textPath href="#anis-ring" startOffset="55%" text-anchor="middle">BEI MAGENSCHMERZEN</textPath></text>
  </svg>

  <!-- Kräutermischung -->
  <svg class="label label--kraeuter" viewBox="0 0 600 600">
    <defs>
      <path id="kraeuter-ring" d="M50 300 a250 250 0 1 0 500 0 a250 250 0 1 0 -500 0"/>
      <path id="kraeuter-brand" d="M200 300 a100 100 0 1 1 200 0 a100 100 0 1 1 -200 0"/>
      <path id="kraeuter-tag" d="M140 300 a160 160 0 1 1 320 0 a160 160 0 1 1 -320 0"/>
    </defs>
    <circle cx="300" cy="300" r="296" fill="var(--herbs)"/>
    <path class="herb-art" d="M170 385 Q300 440 440 340 Q470 250 430 190 Q450 300 380 370 Q290 420 170 385 Z" fill="#9fb4d6" role="img" aria-label="Illustration eines Kräuterzweigs"/>
    <circle class="brand-dot" cx="300" cy="300" r="90"/>
    <text class="brand-name"><textPath href="#kraeuter-brand" startOffset="20%" text-anchor="middle">MOOSPILLE</textPath></text>
    <text class="tagline"><textPath href="#kraeuter-tag" startOffset="21%" text-anchor="middle">TRADITIONAL SWISS FORMULA</textPath></text>
    <text class="product-name"><textPath href="#kraeuter-ring" startOffset="39%" text-anchor="middle">KRÄUTERMISCHUNG</textPath></text>
    <text class="product-use"><textPath href="#kraeuter-ring" startOffset="75%" text-anchor="middle">GEGEN HUSTEN</textPath></text>
  </svg>

  <!-- Lakritze -->
  <svg class="label label--lakritze" viewBox="0 0 600 600">
    <defs>
      <path id="lakritze-ring" d="M50 300 a250 250 0 1 0 500 0 a250 250 0 1 0 -500 0"/>
      <path id="lakritze-brand" d="M200 300 a100 100 0 1 1 200 0 a100 100 0 1 1 -200 0"/>
      <path id="lakritze-tag" d="M140 300 a160 160 0 1 1 320 0 a160 160 0 1 1 -320 0"/>
    </defs>
    <circle cx="300" cy="300" r="296" fill="var(--licorice)"/>
    <ellipse class="herb-art" cx="110" cy="200" rx="90" ry="120" fill="#6d6d6d" role="img" aria-label="Illustration einer Süßholzwurzel"/>
    <circle class="brand-dot" cx="300" cy="300" r="90"/>
    <text class="brand-name"><textPath href="#lakritze-brand" startOffset="20%" text-anchor="middle">MOOSPILLE</textPath></text>
    <text class="tagline"><textPath href="#lakritze-tag" startOffset="21%" text-anchor="middle">TRADITIONAL SWISS FORMULA</textPath></text>
    <text class="product-name"><textPath href="#lakritze-ring" startOffset="28%" text-anchor="middle">LAKRITZE</textPath></text>
    <text class="product-use"><textPath href="#lakritze-ring" startOffset="60%" text-anchor="middle">BEI BLUTHOCHDRUCK</textPath></text>
  </svg>

</main>
</body>
</html>
```